Business Card Design (NEW FILES)

ATTENTION: New vector files are available. Please update your design to reflect/use the new (better resolution) logo images.

Seeking a unique and professional business card design for a commercial drone photography/videography business. The layout should feature
the logo (attached) and include the following information:
Owen Tarrick
614-502-7738
www.skylarkreelworks.example
NRD Certified Remote Pilot

Owen Tarrick

```html
<!DOCTYPE html>
<html lang="en">
<head>
<meta charset="UTF-8">
<title>Skylark Reelworks – Business Card</title>
<link href="https://fonts.googleapis.com/css2?family=Open+Sans:wght@400;600;700&display=swap" rel="stylesheet">
<style>
  :root{
    --stage:#222222;
    --navy:#131848;
    --navy-raised:#1c2674;
    --orange:#ee8a4f;
    --white:#ffffff;
    --line:#b0663c;
  }
  *{margin:0;padding:0;box-sizing:border-box}
  html,body{width:1200px;height:780px;overflow:hidden;background:var(--stage)}
  body{position:relative;font-family:"Open Sans",Arial,sans-serif}
  .card{position:absolute;width:520px;height:297px;background:var(--navy);overflow:hidden;
        box-shadow:0 14px 30px rgba(0,0,0,.5)}
  .card--front{left:50px;top:240px}
  .card--back{left:630px;top:240px}

  .brand{position:absolute;left:34px;top:62px;display:flex;align-items:center;gap:10px;
         color:var(--white);font-weight:400;font-size:22px;letter-spacing:.5px}
  .brand__dot{width:16px;height:16px;border-radius:50%;background:var(--orange);flex:none}

  .divider{position:absolute;left:262px;top:58px;width:1px;height:118px;background:var(--line)}

  .contact{position:absolute;left:282px;top:70px;color:var(--white)}
  .contact__name{font-size:27px;font-weight:700;line-height:1.05}
  .contact__first{color:var(--orange)}
  .contact__role{font-size:13px;margin-top:2px;margin-bottom:12px}
  .contact__row{display:flex;align-items:center;gap:8px;font-size:13px;line-height:20px}
  .contact__row svg{width:12px;height:12px;flex:none}

  .credential-band{position:absolute;left:0;top:236px;width:430px;height:30px;background:var(--orange);
                   color:var(--white);font-size:13px;font-weight:600;line-height:30px;padding-left:22px}
  .aircraft-art{position:absolute;right:0;top:196px;width:130px;height:101px;
                background:linear-gradient(160deg,var(--orange) 0%,var(--white) 55%)}

  .brand--embossed{left:50%;top:50%;transform:translate(-50%,-50%);color:var(--navy-raised);font-size:34px}
  .brand--embossed .brand__dot{width:24px;height:24px;background:var(--navy-raised)}
</style>
</head>
<body>
  <section class="card card--front">
    <div class="brand"><span class="brand__dot"></span>Skylark Reelworks</div>
    <div class="divider"></div>
    <div class="contact">
      <div class="contact__name"><span class="contact__first">Owen</span> Tarrick</div>
      <div class="contact__role">Owner</div>
      <div class="contact__row">
        <svg viewBox="0 0 24 24"><path fill="#ee8a4f" d="M6.6 10.8a15 15 0 0 0 6.6 6.6l2.2-2.2a1 1 0 0 1 1-.25 11.4 11.4 0 0 0 3.6.6 1 1 0 0 1 1 1V20a1 1 0 0 1-1 1A17 17 0 0 1 3 4a1 1 0 0 1 1-1h3.5a1 1 0 0 1 1 1c0 1.25.2 2.45.6 3.6a1 1 0 0 1-.25 1z"/></svg>
        614-502-7738
      </div>
      <div class="contact__row">
        <svg viewBox="0 0 24 24"><circle cx="12" cy="12" r="10" fill="none" stroke="#ee8a4f" stroke-width="2.5"/><path d="M2 12h20M12 2c3 3 3 17 0 20M12 2c-3 3-3 17 0 20" fill="none" stroke="#ee8a4f" stroke-width="2"/></svg>
        www.skylarkreelworks.example
      </div>
      <div class="contact__row">
        <svg viewBox="0 0 24 24"><rect x="2" y="5" width="20" height="14" rx="1" fill="none" stroke="#ee8a4f" stroke-width="2.5"/><path d="M2 6l10 7 10-7" fill="none" stroke="#ee8a4f" stroke-width="2.5"/></svg>
        info@skylarkreelworks.example
      </div>
    </div>
    <div class="credential-band">NRD Certified Remote Pilot, Fully Insured</div>
    <div class="aircraft-art" role="img" aria-label="White drone illustration with camera lens"></div>
  </section>

  <section class="card card--back">
    <div class="brand brand--embossed"><span class="brand__dot"></span>Skylark Reelworks</div>
  </section>
</body>
</html>
```